Business Card Design

I already have a company logo for my company. I have a logo for the manufacturer we represent. I want a professional business card design.

```html
<!DOCTYPE html>
<html lang="en">
<head>
<meta charset="utf-8">
<title>Beacon Safety Group – Business Card</title>
<link rel="stylesheet" href="https://fonts.googleapis.com/css2?family=Poppins:wght@400;700&display=swap">
<style>
  :root {
    --backdrop: #a9a9a9;
    --card: #1b1b1c;
    --red: #e31e2d;
    --white: #f2f2f2;
  }
  * { margin: 0; padding: 0; box-sizing: border-box; }
  html, body {
    width: 1093px; height: 1200px; overflow: hidden;
    background: var(--backdrop);
    font-family: "Poppins", sans-serif;
  }
  .canvas { position: relative; width: 1093px; height: 1200px; }
  .card {
    position: absolute; left: 265px; width: 580px; height: 359px;
    background: var(--card); border-radius: 24px; overflow: hidden;
  }
  .card--front { top: 226px; }
  .card--back { top: 621px; }

  .person { position: absolute; left: 39px; top: 46px; }
  .person__name { color: var(--red); font-weight: 700; font-size: 23px; line-height: 1; letter-spacing: 0.2px; }
  .person__title { color: var(--white); font-weight: 400; font-size: 16.5px; line-height: 1.2; margin-top: 1px; }

  .rule { position: absolute; left: 39px; width: 67px; height: 1px; background: var(--red); }
  .rule--top { top: 118px; }
  .rule--bottom { top: 234px; }

  .contacts { position: absolute; left: 39px; top: 145px; list-style: none; }
  .contacts li {
    display: flex; align-items: center; gap: 7px;
    color: var(--white); font-size: 17.5px; line-height: 21px;
  }
  .contacts svg { width: 15px; height: 15px; flex: none; }
  .accent { color: var(--red); }

  .address { position: absolute; left: 39px; top: 271px; color: var(--white); font-size: 17px; line-height: 21px; }

  .brand {
    position: absolute; color: var(--white); font-weight: 700;
    text-align: center; text-transform: uppercase; line-height: 1.05;
  }
  .card--front .brand { left: 300px; top: 110px; width: 250px; font-size: 40px; }
  .card--back .brand { left: 0; top: 118px; width: 580px; font-size: 42px; }
</style>
</head>
<body>
<div class="canvas">
  <section class="card card--front">
    <div class="person">
      <p class="person__name">DANIEL HARPER</p>
      <p class="person__title">Managing Director</p>
    </div>
    <span class="rule rule--top"></span>
    <ul class="contacts">
      <li>
        <svg viewBox="0 0 24 24" fill="none" stroke="#e31e2d" stroke-width="2.2" stroke-linecap="round" stroke-linejoin="round"><path d="M5 3h4l2 5-2.5 1.5a11 11 0 0 0 6 6L16 13l5 2v4a2 2 0 0 1-2 2A17 17 0 0 1 3 5a2 2 0 0 1 2-2"/></svg>
        044-987 654 321
      </li>
      <li>
        <svg viewBox="0 0 24 24"><rect x="1" y="5" width="22" height="14" fill="#e31e2d"/><path d="M1 5l11 8 11-8" fill="none" stroke="#1b1b1c" stroke-width="1.6"/></svg>
        hello@beaconsg.com
      </li>
      <li>
        <svg viewBox="0 0 24 24" fill="none" stroke="#e31e2d" stroke-width="1.8"><circle cx="12" cy="12" r="10"/><ellipse cx="12" cy="12" rx="4.5" ry="10"/><path d="M2 12h20M4 7h16M4 17h16"/></svg>
        <span>www.<span class="accent">beaconsafety</span>.com</span>
      </li>
    </ul>
    <span class="rule rule--bottom"></span>
    <p class="address">421, Address line goes here<br>45452,Country Name</p>
    <p class="brand">Beacon<br>Safety<br>Group</p>
  </section>

  <section class="card card--back">
    <p class="brand">Beacon<br>Safety Group</p>
  </section>
</div>
</body>
</html>
```